female esthetician looking for an impact business card

I an an expert in skin care industry with high experience in NYC.I want my business card to look professional , an impact at first look. I do want a combination between white and gold . I believe the font will be great if is gold.. The Fonts are also important. MIRABELA COSTINA (SKIN CARE BOUTIQUE)

THIS SHOULD BE THE BUSINESS NAME, and should be placed on th eback of the card.
IN front m, the name MIRABELA COSTINA - ESTHETCIAN

BY APPOINTMENTS ONLY: 518.240.7136

Target Market(s)

HIGH END CLIENTELE

Contact Information for Business Card

iT WILL BE on a luxury paper. I neeed the wow feeling

Requirements
Should not have
• pictures

```html
<!DOCTYPE html>
<html lang="en">
<head>
<meta charset="utf-8">
<title>Mirabela Costina – Business Card</title>
<link rel="stylesheet" href="https://fonts.googleapis.com/css2?family=Cinzel:wght@400&family=Josefin+Sans:wght@300&family=Lato:wght@400;700&display=swap">
<style>
  :root {
    --backdrop: #666666;
    --card: #1f1f1f;
    --gold: #f2cd1d;
    --ink-light: #f1f1f1;
    --ink-muted: #c9c9c9;
    --divider: #5a5a5a;
  }
  * { margin: 0; padding: 0; box-sizing: border-box; }
  html, body {
    width: 1200px; height: 900px; overflow: hidden;
    background: var(--backdrop);
  }
  .canvas { position: relative; width: 1200px; height: 900px; }

  .card {
    position: absolute;
    background: var(--card);
    box-shadow: 2px 3px 6px rgba(0,0,0,0.35);
  }
  .card--front {
    left: 120px; top: 275px; width: 478px; height: 297px;
    border-radius: 0 52px 0 52px;
  }
  .card--back {
    left: 620px; top: 275px; width: 477px; height: 295px;
    border-radius: 52px 0 52px 0;
  }

  .ornament-frame {
    position: absolute;
    background: linear-gradient(135deg, #f4d532, #e2b90f);
    border-radius: 4px;
    opacity: 0.9;
  }
  .card--front .ornament-frame { left: 48px; top: 83px; width: 157px; height: 124px; }
  .card--back .ornament-frame { left: 188px; top: 75px; width: 100px; height: 82px; }

  .divider {
    position: absolute; left: 238px; top: 85px;
    width: 1px; height: 124px; background: var(--divider);
  }

  .contact-block {
    position: absolute; left: 265px; top: 80px;
    font-family: "Lato", sans-serif; color: var(--ink-light);
  }
  .contact-name {
    font-weight: 700; font-size: 17.5px; color: var(--gold);
    line-height: 20px; letter-spacing: 0.1px;
  }
  .contact-title { font-size: 12.5px; line-height: 15px; margin-bottom: 6px; }
  .contact-line {
    display: flex; align-items: center; gap: 5px;
    font-size: 13px; line-height: 19px;
  }
  .contact-line svg { width: 11px; height: 11px; flex: none; }
  .contact-address { font-size: 12.5px; line-height: 15.5px; margin-top: 8px; }

  .brand-name {
    position: absolute; left: 0; right: 0; top: 167px;
    text-align: center;
    font-family: "Cinzel", serif; font-size: 29px; color: var(--gold);
    letter-spacing: 1.6px;
  }
  .brand-tagline {
    position: absolute; left: 0; right: 0; top: 206px;
    text-align: center;
    font-family: "Josefin Sans", sans-serif; font-weight: 300;
    font-size: 11px; color: var(--ink-muted);
    letter-spacing: 5.4px; padding-left: 5px;
  }
</style>
</head>
<body>
<main class="canvas">

  <section class="card card--front" aria-label="Card front">
    <div class="ornament-frame" role="img" aria-label="Gold ornamental scroll frame"></div>
    <div class="divider"></div>
    <div class="contact-block">
      <p class="contact-name">MIRABELA COSTINA</p>
      <p class="contact-title">MANAGING DIRECTOR</p>
      <p class="contact-line">
        <svg viewBox="0 0 12 12" aria-hidden="true"><path fill="var(--gold)" d="M1 4c0-1.5 2-2.5 5-2.5S11 2.5 11 4v1H8.5V4h-5v1H1zM3 6h6l1.5 4.5h-9z"/></svg>
        518.240.7136
      </p>
      <p class="contact-line">
        <svg viewBox="0 0 12 12" aria-hidden="true"><rect x="0.5" y="2.5" width="11" height="7" fill="var(--gold)"/><path d="M0.5 2.5 6 6.5l5.5-4" fill="none" stroke="var(--card)" stroke-width="1"/></svg>
        INFO@COSTINASKIN.COM
      </p>
      <p class="contact-line">
        <svg viewBox="0 0 12 12" aria-hidden="true"><circle cx="6" cy="6" r="5.5" fill="var(--gold)"/><path d="M3 4.5c1-.5 2 0 2.5 1S4.5 8 4 9M7.5 2.5c.5 1 1.5 1.5 2.5 1.5M7 7.5c1 0 1.5 1 1.5 2" fill="none" stroke="var(--card)" stroke-width="1"/></svg>
        WWW.COSTINASKIN.COM
      </p>
      <p class="contact-address">218, LINDEN AVENUE<br>NEW YORK, NY 10012</p>
    </div>
  </section>

  <section class="card card--back" aria-label="Card back">
    <div class="ornament-frame" role="img" aria-label="Small gold ornamental scroll frame"></div>
    <h1 class="brand-name">MIRABELA COSTINA</h1>
    <p class="brand-tagline">SKIN CARE EXPERT</p>
  </section>

</main>
</body>
</html>
```